Buch-Cover für Lichtblick gesucht
Zielgruppe
Wir sind eine Firma die hochwertige Fitnessprodukte produziert und vertreibt. Unsere Zielgruppe sind gesundheitsbewusste Frauen ab Mitte 20 bis open end, die hohe Ansprüche an sich selbst stellen und sich für das Thema Selbstoptimierung interessieren.
Aufgabenstellung
Es soll ein Hardcover gestaltet werden.
Buchtitel: Lichtblick, Untertitel: Ein Sommer voller Mut
Detaillierte Beschreibung der Projektanforderungen siehe Anhang Projektbeschreibung. Darüber hinaus bin ich auch für alternative Gestaltungs-Ideen offen.
Das Design soll der Käuferin folgendes vermitteln:
- Wertigkeit
- Positivität
und sie ein bisschen träumen lassen und natürlich neugierig auf den Inhalt machen.

```html
<!DOCTYPE html>
<html lang="de">
<head>
<meta charset="utf-8">
<title>Lichtblick – Buchumschlag</title>
<link rel="stylesheet" href="https://fonts.googleapis.com/css2?family=EB+Garamond&family=Yesteryear&family=Caveat:wght@600&display=swap">
<style>
  :root {
    --pink: #f0508f;
    --pink-deep: #d93a78;
    --gold: #f6c229;
    --panel: #f3d5bc;
    --ink: #1d1715;
    --spine: #4b4342;
    --paper: #fdfbfa;
  }
  * { margin: 0; padding: 0; box-sizing: border-box; }
  html, body { width: 1200px; height: 894px; overflow: hidden; background: #fff; }
  .cover { position: relative; width: 1200px; height: 894px; overflow: hidden; }

  .back-photo {
    position: absolute; left: 0; top: 0; width: 552px; height: 894px;
    background:
      radial-gradient(circle at 60% 8%, #f4e0a8 0, transparent 40%),
      radial-gradient(circle at 10% 60%, #2c2428 0, transparent 45%),
      radial-gradient(circle at 40% 92%, #c99a66 0, transparent 40%),
      linear-gradient(180deg, #e8d7a6 0%, #b89f7d 35%, #5a4a4c 70%, #8d6f5e 100%);
  }
  .front-photo {
    position: absolute; left: 642px; top: 0; width: 558px; height: 894px;
    background:
      radial-gradient(ellipse at 85% 55%, #e9c8a0 0, transparent 40%),
      radial-gradient(ellipse at 35% 80%, #2d2826 0, transparent 45%),
      radial-gradient(ellipse at 50% 30%, #e4d2ba 0, transparent 50%),
      linear-gradient(180deg, #ddd4cc 0%, #b99d83 40%, #6a5a50 70%, #c49a74 100%);
  }

  .back-panel {
    position: absolute; left: 50px; top: 68px; width: 469px; height: 632px;
    background: var(--panel);
    box-shadow: 0 0 18px 8px rgba(243, 213, 188, .75);
  }
  .back-heading {
    position: absolute; left: 66px; top: 104px; width: 436px;
    display: flex; align-items: center; justify-content: space-between;
  }
  .back-heading h2 {
    font-family: "Yesteryear", cursive; font-weight: 400;
    color: var(--pink-deep); font-size: 40px; line-height: 1;
    text-shadow: 1px 1px 1px rgba(0,0,0,.25);
  }
  .back-heading svg { width: 62px; height: 16px; }
  .blurb {
    position: absolute; left: 68px; top: 202px; width: 450px;
    font-family: "EB Garamond", serif; font-size: 18.4px; line-height: 21.8px;
    color: var(--ink);
  }
  .blurb p + p { margin-top: 21.8px; }
  .barcode-space {
    position: absolute; left: 311px; top: 723px; width: 217px; height: 131px;
    background: var(--paper);
  }

  .spine {
    position: absolute; left: 552px; top: 0; width: 90px; height: 894px;
    background: var(--spine);
  }
  .spine-imprint {
    position: absolute; left: 0; top: 60px; width: 90px; text-align: center;
    font-family: "Caveat", cursive; font-weight: 600; font-size: 20px; color: var(--gold);
  }
  .spine-title, .spine-author {
    position: absolute; left: 45px; white-space: nowrap;
    transform: translate(-50%, -50%) rotate(90deg);
  }
  .spine-title {
    top: 448px; font-family: "Yesteryear", cursive; font-size: 58px; color: var(--pink);
  }
  .spine-author {
    top: 772px; font-family: "Caveat", cursive; font-weight: 600; font-size: 34px; color: var(--gold);
  }

  .front-title {
    position: absolute; left: 684px; top: 20px;
    font-family: "Yesteryear", cursive; font-weight: 400; font-size: 150px; line-height: 1.1;
    color: var(--pink); text-shadow: 2px 3px 3px rgba(0,0,0,.35);
  }
  .front-subtitle {
    position: absolute; left: 676px; top: 228px; width: 500px; text-align: center;
    font-family: "Caveat", cursive; font-weight: 600; font-size: 52px;
    color: var(--gold); text-shadow: 1px 2px 2px rgba(0,0,0,.35);
  }
</style>
</head>
<body>
<div class="cover">
  <div class="back-photo" role="img" aria-label="Unscharfer Hintergrund mit warmen Lichtreflexen einer Sommerfahrt"></div>

  <div class="back-panel"></div>
  <div class="back-heading">
    <svg viewBox="0 0 62 16" aria-hidden="true"><path d="M2 4 L8 8 L2 12 M4 8 H56" stroke="var(--pink-deep)" stroke-width="2.5" fill="none"/><path d="M54 4 L60 8 L54 12 Z" fill="var(--pink-deep)"/></svg>
    <h2>Was zählt wirklich?</h2>
    <svg viewBox="0 0 62 16" aria-hidden="true"><path d="M8 4 L2 8 L8 12 Z" fill="var(--pink-deep)"/><path d="M6 8 H58 M60 4 L54 8 L60 12" stroke="var(--pink-deep)" stroke-width="2.5" fill="none"/></svg>
  </div>
  <div class="blurb">
    <p>Ich habe mich oft gefragt: Wie soll ich bloß die Liebe und Bestätigung, die mir damals in meiner Kindheit verwehrt blieben, „nachholen“? Lösungsansätze für mein Problem hatte ich in der Vergangenheit durchaus: Ich versuchte das Loch in mir mit Hilfe zur Selbsthilfe, Erfolg im Job und Konsum zu stopfen. Und meine Partner mussten auch für so einiges herhalten.</p>
    <p>Von Gott wollte ich lange nichts wissen. Schließlich hatte er es zugelassen, dass mir sehr viel Unheil in meinem Leben widerfahren ist. Und deshalb war ich echt wütend auf ihn.</p>
    <p>Heutzutage bin ich mir sicher, dass ich mit dieser Denkweise meine Lebenszeit verschwendet habe. Letzten Sommer begriff ich endlich: im Leben gilt die gleiche Gesetzmäßigkeit wie beim Autofahren. Der Rückspiegel ist so klein und die Frontscheibe so groß, weil das was vor uns liegt, viel wichtiger ist, als das was hinter uns liegt. Aufgrund dieser Erkenntnis entschied ich mich, einen völlig neuen Weg einzuschlagen und wagte mich auf eine spannende Reise, die mein Leben für immer veränderte …</p>
  </div>
  <div class="barcode-space"></div>

  <div class="spine">
    <div class="spine-imprint">kesmuro</div>
    <div class="spine-title">Lichtblick</div>
    <div class="spine-author">Marte Quisselt</div>
  </div>

  <div class="front-photo" role="img" aria-label="Foto: Frau mit Sonnenbrille am Steuer eines Cabrios auf sonniger Landstraße, Blick über die Schulter nach vorn"></div>
  <h1 class="front-title">Lichtblick</h1>
  <div class="front-subtitle">Ein Sommer voller Mut</div>
</div>
</body>
</html>
```